Redesign business cards

We have a new logo and I am not that happy with the layout of our existing card and looking for a change. Font is a bit small and the green can be hard to read. Logo may need a tidy up as the copy I have is not that hi-res too so require you to produce a hi-res version of the logo for us too. There will be three individual business cards to produce with just the names and phone numbers being different. Address will change too, but use what you see on the card for now.

Industry/Entity Type

Business

Requirements
Nice to have
• You could consider a redesign to the new logo, just not too radical. We like the blue and green hexagons as we feel that they are representative of oil industry that we are in.

```html
<!DOCTYPE html>
<html lang="en">
<head>
<meta charset="utf-8">
<title>PetroCell Oil Services – Business Card</title>
<link href="https://fonts.googleapis.com/css2?family=Arimo:wght@400;700&display=swap" rel="stylesheet">
<style>
  :root {
    --backdrop: #3e4a54;
    --card: #ffffff;
    --brand-blue: #1ea8e0;
    --brand-green: #7fbf3a;
    --ink: #1a1a1a;
    --icon-grey: #8a8f94;
    --on-band: #ffffff;
  }
  html, body {
    margin: 0;
    width: 1200px;
    height: 1000px;
    overflow: hidden;
    background: var(--backdrop);
    font-family: "Arimo", Arial, sans-serif;
  }
  .business-card {
    position: absolute;
    left: 150px;
    top: 243px;
    width: 900px;
    height: 514px;
    background: var(--card);
    overflow: hidden;
    box-shadow: 0 10px 30px rgba(0,0,0,0.35);
  }
  .wave-band {
    position: absolute;
    inset: 0;
    width: 900px;
    height: 514px;
  }
  .person {
    position: absolute;
    right: 44px;
    top: 40px;
    text-align: right;
  }
  .person-name {
    margin: 0;
    color: var(--brand-blue);
    font-size: 30px;
    font-weight: 400;
  }
  .person-role {
    margin: 6px 0 0;
    color: var(--brand-green);
    font-size: 24px;
  }
  .contact-list {
    position: absolute;
    left: 540px;
    top: 170px;
    margin: 0;
    padding: 0;
    list-style: none;
    font-size: 26px;
    color: var(--ink);
  }
  .contact-list li {
    display: flex;
    align-items: center;
    gap: 14px;
    height: 36px;
    white-space: nowrap;
  }
  .contact-icon {
    width: 20px;
    height: 20px;
    flex: none;
  }
  .brand {
    position: absolute;
    left: 70px;
    top: 180px;
    display: flex;
    align-items: center;
    gap: 16px;
  }
  .brand-mark {
    width: 34px;
    height: 34px;
    border-radius: 50%;
    background: var(--brand-blue);
  }
  .brand-name {
    color: var(--brand-blue);
    font-size: 46px;
    font-weight: 700;
    line-height: 1.05;
  }
  .address {
    position: absolute;
    left: 36px;
    bottom: 34px;
    display: flex;
    align-items: center;
    gap: 12px;
    color: var(--on-band);
    font-size: 19px;
    white-space: nowrap;
  }
  .address svg { width: 18px; height: 24px; flex: none; }
</style>
</head>
<body>
  <article class="business-card">
    <svg class="wave-band" viewBox="0 0 900 514" aria-hidden="true">
      <path d="M0,400 C260,385 560,355 900,300 L900,514 L0,514 Z" fill="var(--brand-green)"/>
      <path d="M0,428 C280,420 580,385 900,322 L900,514 L0,514 Z" fill="var(--brand-blue)"/>
    </svg>

    <header class="person">
      <h1 class="person-name">Daniel Whitford NZCE (Mech) P&amp;P</h1>
      <p class="person-role">Director</p>
    </header>

    <div class="brand">
      <span class="brand-mark"></span>
      <span class="brand-name">PetroCell<br>Oil Services</span>
    </div>

    <ul class="contact-list">
      <li>
        <svg class="contact-icon" viewBox="0 0 24 24"><path fill="var(--icon-grey)" d="M6.6 10.8a15 15 0 0 0 6.6 6.6l2.2-2.2c.3-.3.7-.4 1-.2 1.1.4 2.3.6 3.6.6.6 0 1 .4 1 1V20c0 .6-.4 1-1 1A17 17 0 0 1 3 4c0-.6.4-1 1-1h3.5c.6 0 1 .4 1 1 0 1.3.2 2.5.6 3.6.1.3 0 .7-.2 1z"/></svg>
        +614 555 01842
      </li>
      <li>
        <svg class="contact-icon" viewBox="0 0 24 24"><rect x="2" y="5" width="20" height="14" rx="1" fill="var(--icon-grey)"/><path d="M2 6l10 7 10-7" stroke="#fff" stroke-width="1.6" fill="none"/></svg>
        daniel@petrocell.co.nz
      </li>
      <li>
        <svg class="contact-icon" viewBox="0 0 24 24" fill="none" stroke="var(--icon-grey)" stroke-width="1.6"><circle cx="12" cy="12" r="9"/><ellipse cx="12" cy="12" rx="4" ry="9"/><path d="M3 12h18M5 7h14M5 17h14"/></svg>
        www.petrocell.com.au
      </li>
    </ul>

    <footer class="address">
      <svg viewBox="0 0 18 24"><path fill="var(--on-band)" d="M9 0a9 9 0 0 0-9 9c0 6.5 9 15 9 15s9-8.5 9-15a9 9 0 0 0-9-9zm0 12.5A3.5 3.5 0 1 1 9 5.5a3.5 3.5 0 0 1 0 7z"/></svg>
      PetroCell Oil Services 415 Harbour Road / PO Box 3190 / Kelvin Grove Queensland 4059
    </footer>
  </article>
</body>
</html>
```